Plakat-Design Workshop gegen Prüfungsangst
Zielgruppe
Prüfungsangst überwinden mittels Workshops: 'Selbsthypnose erlernen'
Zielgruppe Studenten
Schweißausbrüche, Blackout, und Resignation.
Viele kennen diese unangenehmen Momente, wenn eine Prüfung begonnen hat und die Aufgabenstellungen scheinbar unlösbar sind.
Dann ist Entspannung nahezu unmöglich. Das Stresshormon Cortisol wurde bereits ausgeschüttet. Es beeinträchtigt die Erinnerung an das Gelernte.
Die mentale Vorbereitung sollte schon viel eher ansetzen, wenn es noch nicht zu spät ist. Wenn der Körper noch nicht verkrampft ist.
Selbsthypnose vor Prüfungen ist hier eine tolle Möglichkeit.
Mit Hilfe einer geführten Selbsthypnoseanleitung ist es Dir möglich Dein Unterbewusstsein so zu programmieren, dass diese Übererregungszustände vor Prüfungssituationen deutlich reduziert werden.
Aufgabenstellung
DINA 4 Plakat, 'Prüfungsangst?' mit einem Freifeld, wo man Ort, Datum und Zeit der Veranstaltung 'Selbsthypnose erlernen'
(Selbstsicher in die Prüfung) eindrucken kann.
darunter:
Anmeldung: Tel: 01563 8074215
Dipl. Sportl. Henrik Wolde Mentaltraining
weitere Infos auch über Einzelsitzungen: www.wolde-trancepraxis.de

```html
<!DOCTYPE html>
<html lang="de">
<head>
<meta charset="utf-8">
<title>Prüfungsangst? – Workshop Selbsthypnose</title>
<link href="https://fonts.googleapis.com/css2?family=Hind:wght@300;400;500;600;700&display=swap" rel="stylesheet">
<style>
  :root {
    --blue: #1d56a4;
    --ink: #111111;
    --paper: #ffffff;
    --photo-a: #d9d6d2;
    --photo-b: #b9b6b4;
    --portrait-a: #a9a6a2;
    --portrait-b: #c7d3e6;
    --badge: #2a8c98;
  }
  html, body {
    margin: 0;
    padding: 0;
    width: 881px;
    height: 1200px;
    overflow: hidden;
    background: var(--paper);
  }
  .poster {
    position: relative;
    width: 881px;
    height: 1200px;
    background: var(--paper);
    font-family: "Hind", Arial, sans-serif;
    color: var(--ink);
    overflow: hidden;
  }
  .hero { position: absolute; left: 0; top: 0; width: 881px; height: 338px; }
  .hero-rule { position: absolute; left: 0; top: 395px; width: 881px; height: 5px; background: var(--ink); }
  .headline {
    position: absolute; left: 30px; top: 392px; margin: 0;
    font-size: 118px; font-weight: 500; line-height: 1; color: var(--blue);
    letter-spacing: -1px;
  }
  .symptoms {
    position: absolute; left: 32px; top: 505px; margin: 0;
    font-size: 39px; font-weight: 600; line-height: 1; color: var(--ink);
  }
  .intro {
    position: absolute; left: 32px; top: 560px; width: 820px; margin: 0;
    font-size: 22.5px; font-weight: 400; line-height: 31.5px;
  }
  .claim {
    position: absolute; left: 32px; top: 718px; margin: 0;
    font-size: 55px; font-weight: 600; line-height: 1; color: var(--blue);
  }
  .footer-band { position: absolute; left: 0; top: 1159px; width: 881px; height: 41px; background: var(--blue); }
  .portrait {
    position: absolute; left: 33px; top: 783px; width: 293px; height: 403px;
    background: linear-gradient(180deg, var(--portrait-a) 0%, #9d9b98 45%, var(--portrait-b) 100%);
  }
  .seal {
    position: absolute; left: 245px; top: 1043px; width: 120px; height: 120px;
    border-radius: 50%; background: var(--paper);
    box-shadow: 0 0 0 3px var(--paper);
  }
  .seal::after {
    content: ""; position: absolute; left: 18px; top: 18px; width: 84px; height: 84px;
    border-radius: 50%; background: var(--badge);
  }
  .event {
    position: absolute; left: 393px; top: 772px; margin: 0;
    font-size: 46px; font-weight: 400; line-height: 53.5px;
  }
  .event span { display: block; }
  .brand {
    position: absolute; left: 393px; top: 966px; width: 191px; height: 78px;
    background: var(--ink); color: var(--paper);
    display: flex; align-items: center; justify-content: center;
    font-size: 17px; font-weight: 700; letter-spacing: 1px;
  }
  .registration {
    position: absolute; left: 393px; top: 1048px; margin: 0;
    font-size: 17.5px; line-height: 21px; font-weight: 400;
  }
  .registration strong { font-weight: 600; }
  .registration span { display: block; }
</style>
</head>
<body>
<main class="poster">
  <svg class="hero" viewBox="0 0 881 338" aria-hidden="false">
    <defs>
      <linearGradient id="photoTone" x1="0" y1="0" x2="0" y2="1">
        <stop offset="0" stop-color="#e4e2df"/>
        <stop offset="1" stop-color="#b3b1af"/>
      </linearGradient>
    </defs>
    <rect x="0" y="0" width="881" height="338" fill="var(--blue)"/>
    <polygon role="img" aria-label="Foto: angespannte Studentin am Schreibtisch über Büchern"
      points="21,20 341,20 488,168 350,317 21,317" fill="url(#photoTone)"/>
    <polygon role="img" aria-label="Foto: dieselbe Studentin entspannt und lächelnd am Schreibtisch"
      points="392,20 860,20 860,317 398,317 534,168" fill="url(#photoTone)"/>
  </svg>
  <div class="hero-rule"></div>

  <h1 class="headline">Prüfungsangst?</h1>
  <h2 class="symptoms">Schweißausbrüche, Blackout &amp; Resignation?</h2>
  <p class="intro">Mit Hilfe einer geführten Selbsthypnoseanleitung ist es Dir möglich<br>Dein Unterbewusstsein so zu programmieren, dass diese Übererregungs-<br>zustände vor Prüfungssituationen deutlich reduziert werden.</p>

  <h2 class="claim">Selbstsicher in die Prüfung!</h2>

  <div class="footer-band"></div>
  <div class="portrait" role="img" aria-label="Porträtfoto des Mentaltrainers vor einer Betonwand"></div>
  <div class="seal" role="img" aria-label="Zertifizierungssiegel"></div>

  <p class="event">
    <span>12345 Musterstadt</span>
    <span>29/09/2020</span>
    <span>20.00 Uhr</span>
  </p>

  <div class="brand">WOLDE-TRANCE</div>

  <p class="registration">
    <strong>Anmeldung:</strong>
    <span>Tel: 01563 8074215</span>
    <span>Dipl. Sportl. Henrik Wolde Mentaltraining</span>
    <span>weitere Infos auch über Einzelsitzungen:</span>
    <span>www.wolde-trancepraxis.de</span>
  </p>
</main>
</body>
</html>
```